Business Card Design Project

This is the first time we use our new logo. We need a business card that we can use both on our institutional corporate relationships and also that works for our staff that deals with consumers directly.

VELUNDA is a new company dedicated to empower consumers and to provide them with the best choices for specialized health care using the latest telemedicine technology (medicine at a distance via videoconference).

We want to print this cards in high quality materials and process. We will like designs that allow us to use UV spot varnish and other techniques that will differentiate us.

We are including Two different versions of Color logos. In addition we are including white over black background logos. Those can be used replacing the black for a color.

Please note this is the first time we will be creating any corporate materials with our new logo and colors.

Target Market(s)

34+ consumers of medium high and high socioeconomic levels.

Industry/Entity Type

Health

Requirements
Must have
• Our logo on its original colors
Should not have
• Any other graphical element or design that is not our logo

```html
<!DOCTYPE html>
<html lang="en">
<head>
<meta charset="utf-8">
<title>VELUNDA Business Card</title>
<link rel="stylesheet" href="https://fonts.googleapis.com/css2?family=Jost:wght@500;600&family=Arimo:wght@400&display=swap">
<style>
  :root {
    --page-bg: #e8e6e1;
    --card-bg: #efe2c6;
    --brand-navy: #1c5a88;
    --brand-teal: #2aa79b;
    --brand-sky: #4fb5e0;
    --divider: #4a4a4a;
    --body-text: #262626;
    --white: #ffffff;
  }
  * { margin: 0; padding: 0; box-sizing: border-box; }
  html, body {
    width: 1200px;
    height: 868px;
    overflow: hidden;
    background: var(--page-bg);
  }
  .card {
    position: absolute;
    left: 100px;
    top: 148px;
    width: 1000px;
    height: 572px;
    background: var(--card-bg);
    box-shadow: 0 2px 10px rgba(0,0,0,0.12);
    overflow: hidden;
  }
  .brand-name {
    position: absolute;
    left: 64px;
    top: 362px;
    width: 440px;
    text-align: center;
    font-family: "Jost", sans-serif;
    font-weight: 600;
    font-size: 88px;
    line-height: 1;
    letter-spacing: 2px;
    color: var(--brand-navy);
  }
  .divider {
    position: absolute;
    left: 557px;
    top: 80px;
    width: 2px;
    height: 392px;
    background: var(--divider);
  }
  .contact {
    position: absolute;
    left: 604px;
    top: 96px;
    font-family: "Arimo", sans-serif;
    color: var(--body-text);
  }
  .person-name {
    font-family: "Jost", sans-serif;
    font-weight: 600;
    font-size: 40px;
    line-height: 48px;
    color: var(--brand-navy);
  }
  .person-title {
    font-family: "Arimo", sans-serif;
    font-weight: 400;
    font-size: 29px;
    line-height: 34px;
    color: var(--brand-teal);
  }
  .contact-list {
    list-style: none;
    margin-top: 38px;
  }
  .contact-item {
    display: flex;
    align-items: center;
    gap: 10px;
    font-size: 25px;
    line-height: 44px;
  }
  .contact-icon {
    width: 20px;
    height: 20px;
    flex: none;
  }
  .address {
    margin-top: 30px;
    font-size: 25px;
    line-height: 34px;
  }
  .footer-bands {
    position: absolute;
    left: 0;
    top: 528px;
    width: 1000px;
    height: 44px;
  }
  .website {
    position: absolute;
    left: 545px;
    top: 533px;
    width: 430px;
    text-align: center;
    font-family: "Arimo", sans-serif;
    font-size: 25px;
    line-height: 34px;
    letter-spacing: 4px;
    color: var(--white);
  }
</style>
</head>
<body>
  <main class="card">
    <div class="brand-name">VELUNDA</div>

    <div class="divider" aria-hidden="true"></div>

    <section class="contact">
      <h1 class="person-name">Your Name</h1>
      <p class="person-title">Title</p>
      <ul class="contact-list">
        <li class="contact-item">
          <svg class="contact-icon" viewBox="0 0 20 20" aria-hidden="true">
            <circle cx="10" cy="10" r="8.5" fill="none" stroke="#262626" stroke-width="1.5"/>
            <path d="M7 5.5c-1.5 1.5-1 4.5 1.5 7s5 3 6 1.5l-1.8-1.6-1.3 1c-1.2-.5-2.5-1.8-3-3l1-1.3z" fill="#262626"/>
          </svg>
          <span>012-345-6789</span>
        </li>
        <li class="contact-item">
          <svg class="contact-icon" viewBox="0 0 20 20" aria-hidden="true">
            <circle cx="10" cy="10" r="8.5" fill="none" stroke="#262626" stroke-width="1.5"/>
            <path d="M7 5.5c-1.5 1.5-1 4.5 1.5 7s5 3 6 1.5l-1.8-1.6-1.3 1c-1.2-.5-2.5-1.8-3-3l1-1.3z" fill="#262626"/>
          </svg>
          <span>012-345-6789</span>
        </li>
        <li class="contact-item">
          <svg class="contact-icon" viewBox="0 0 20 20" aria-hidden="true">
            <path d="M2 8l8-5 8 5v8H2z" fill="#262626"/>
            <path d="M4 8.5l6 4 6-4" fill="none" stroke="#efe2c6" stroke-width="1.5"/>
          </svg>
          <span>name@velunda.com</span>
        </li>
      </ul>
      <p class="address">Street Name, City Name<br>State, City Zip Code</p>
    </section>

    <svg class="footer-bands" viewBox="0 0 1000 44" aria-hidden="true">
      <rect x="0" y="23" width="1000" height="21" fill="var(--brand-sky)"/>
      <polygon points="524,0 1000,0 1000,44 486,44" fill="var(--brand-navy)"/>
    </svg>
    <div class="website">www.velunda.com</div>
  </main>
</body>
</html>
```